Simple and Clean business card design

We would like the design to be simple clean and to incorporate our colors.

We are open to your design and talent, we have the dots in our logo as we think of it as data points and we connect data points for people.

We are open to see the great creative and clean design you bring to the table

Contact Information for Business Card

please include: name, position, email, phone and website

Font styles to use
Sans Serif

Requirements
Must have
• my colors incorporated, simplicity
Nice to have
• lots of white space, simplicity
Should not have
• complexicity/ complex art

```html
<!DOCTYPE html>
<html lang="en">
<head>
<meta charset="utf-8">
<title>Nectra — Business Card</title>
<link rel="stylesheet" href="https://fonts.googleapis.com/css2?family=Montserrat:wght@400;500;700&family=Oswald:wght@600&display=swap">
<style>
  :root {
    --backdrop: #262729;
    --brand-blue: #547bc0;
    --brand-green: #34a853;
    --ink: #0d0d0d;
    --paper: #ffffff;
    --rule: #8a8a8a;
  }
  * { box-sizing: border-box; margin: 0; padding: 0; }
  html, body {
    width: 1200px; height: 900px; overflow: hidden;
    background: var(--backdrop);
    font-family: "Montserrat", sans-serif;
  }
  .canvas {
    width: 1200px; height: 900px;
    display: flex; flex-direction: column; align-items: center; justify-content: center;
    gap: 52px;
  }
  .card {
    width: 620px; height: 354px;
    border-radius: 22px;
    position: relative;
    overflow: hidden;
    box-shadow: 0 14px 30px rgba(0,0,0,0.45);
  }
  .card--front {
    background: var(--brand-blue);
    border-bottom: 6px solid var(--brand-green);
    display: flex; flex-direction: column; align-items: center; justify-content: center;
  }
  .brand-name {
    font-weight: 700; font-size: 96px; line-height: 1;
    color: var(--ink); letter-spacing: -1px;
  }
  .brand-url {
    margin-top: 30px;
    font-size: 17px; color: var(--paper); letter-spacing: 0.5px;
  }
  .brand-url strong { font-weight: 700; }
  .brand-url span { font-weight: 400; }

  .card--back {
    background: var(--paper);
    border-bottom: 6px solid var(--brand-blue);
    display: flex; align-items: center; justify-content: center;
  }
  .identity {
    text-align: right;
    padding-right: 22px;
  }
  .identity__name {
    font-family: "Oswald", sans-serif; font-weight: 600;
    font-size: 46px; line-height: 1; color: var(--ink);
    text-transform: uppercase; letter-spacing: -0.5px;
  }
  .identity__role {
    margin-top: 6px;
    font-size: 16px; font-weight: 500; color: var(--brand-green); letter-spacing: 0.5px;
  }
  .divider {
    width: 1.5px; height: 88px; background: var(--rule);
  }
  .contact-list {
    list-style: none; padding-left: 22px;
    display: flex; flex-direction: column; gap: 7px;
  }
  .contact-list li {
    display: flex; align-items: center; gap: 10px;
    font-size: 15px; font-weight: 500; color: var(--ink); letter-spacing: 0.3px;
  }
  .contact-list .accent { color: var(--brand-green); }
  .contact-icon { width: 15px; height: 15px; flex: none; }
</style>
</head>
<body>
<main class="canvas">
  <section class="card card--front" aria-label="Card front">
    <p class="brand-name">nectra</p>
    <p class="brand-url"><strong>nectra</strong><span>.one</span></p>
  </section>

  <section class="card card--back" aria-label="Card back">
    <div class="identity">
      <h1 class="identity__name">Liam Corder</h1>
      <p class="identity__role">Founder/ CEO</p>
    </div>
    <div class="divider"></div>
    <ul class="contact-list">
      <li>
        <svg class="contact-icon" viewBox="0 0 16 16" fill="none" stroke="#34a853" stroke-width="1.6"><rect x="4" y="1.5" width="8" height="13" rx="1.5"/><line x1="7" y1="12" x2="9" y2="12"/></svg>
        555-010-2846
      </li>
      <li>
        <svg class="contact-icon" viewBox="0 0 16 16" fill="none" stroke="#34a853" stroke-width="1.6"><rect x="1.5" y="3.5" width="13" height="9" rx="1"/><polyline points="1.5,4 8,9 14.5,4"/></svg>
        <span>liam.corder@<span class="accent">nectra.one</span></span>
      </li>
      <li>
        <svg class="contact-icon" viewBox="0 0 16 16" fill="none" stroke="#34a853" stroke-width="1.6"><circle cx="9" cy="7" r="5"/><line x1="5.5" y1="10.5" x2="2" y2="14"/></svg>
        <span>www.<span class="accent">nectra.one</span></span>
      </li>
    </ul>
  </section>
</main>
</body>
</html>
```